Redesign of business card for Cedar Ridge Mechanical

We are looking for a new design for our business cards for Cedar Ridge Mechanical. We are a plumbing & HVAC construction company, operating on the West Coast of Canada and USA. Logo attached.
Industry/Entity Type
Construction - Plumbing & HVAC
Contact Information for Business Card
Name, address, phone numbers, email, website address
Look and feel
Each slider illustrates characteristics of the customer's brand and the style your logo design should communicate.

```html
<!DOCTYPE html>
<html lang="en">
<head>
<meta charset="utf-8">
<title>Cedar Ridge Mechanical – Business Card</title>
<link rel="stylesheet" href="https://fonts.googleapis.com/css2?family=Montserrat:wght@400;500;600;700&display=swap">
<style>
  :root {
    --backdrop: #e6e0d8;
    --card-frost: #d8cec2;
    --card-frost-light: #e7dfd5;
    --card-dark: #0e0e0e;
    --card-dark-soft: #2a2826;
    --text-gold: #cdbba5;
    --text-muted: #b7a995;
    --logo-ink: #1b1b1b;
    --swoosh: #a9a39c;
  }
  html, body {
    margin: 0;
    padding: 0;
    width: 1200px;
    height: 1047px;
    overflow: hidden;
    background: var(--backdrop);
    font-family: "Montserrat", sans-serif;
  }
  .business-card {
    position: absolute;
    left: 100px;
    top: 248px;
    width: 1000px;
    height: 550px;
    border-radius: 22px;
    overflow: hidden;
    background: linear-gradient(135deg, var(--card-frost-light), var(--card-frost));
    box-shadow: 0 18px 40px rgba(0,0,0,0.18);
  }
  .card-shapes {
    position: absolute;
    inset: 0;
  }
  .contact-block {
    position: absolute;
    left: 46px;
    top: 186px;
    color: var(--text-muted);
  }
  .person-name {
    margin: 0;
    font-size: 33px;
    font-weight: 600;
    letter-spacing: 0.5px;
    color: var(--text-gold);
  }
  .person-title {
    margin: 8px 0 0;
    font-size: 24px;
    font-weight: 400;
  }
  .address {
    margin: 40px 0 0;
    font-size: 24px;
    line-height: 38px;
    font-weight: 400;
  }
  .contact-list {
    list-style: none;
    margin: 32px 0 0;
    padding: 0;
    font-size: 24px;
    font-weight: 400;
  }
  .contact-list li {
    display: flex;
    align-items: center;
    gap: 12px;
    height: 39px;
  }
  .contact-icon {
    width: 20px;
    height: 20px;
    fill: var(--text-muted);
  }
  .brand-mark {
    position: absolute;
    left: 530px;
    top: 128px;
    display: flex;
    align-items: center;
    gap: 16px;
  }
  .brand-square {
    width: 30px;
    height: 30px;
    background: var(--logo-ink);
  }
  .brand-name {
    font-size: 27px;
    font-weight: 600;
    letter-spacing: 1px;
    text-transform: uppercase;
    color: var(--logo-ink);
  }
</style>
</head>
<body>
  <div class="business-card">
    <svg class="card-shapes" viewBox="0 0 1000 550" width="1000" height="550" aria-hidden="true">
      <defs>
        <linearGradient id="darkPanel" x1="0" y1="0" x2="1" y2="1">
          <stop offset="0" stop-color="var(--card-dark-soft)"/>
          <stop offset="0.45" stop-color="var(--card-dark)"/>
          <stop offset="1" stop-color="var(--card-dark)"/>
        </linearGradient>
        <linearGradient id="swooshGlow" x1="0" y1="0" x2="1" y2="1">
          <stop offset="0" stop-color="#f2ede6" stop-opacity="0.9"/>
          <stop offset="0.5" stop-color="var(--swoosh)"/>
          <stop offset="1" stop-color="var(--swoosh)" stop-opacity="0.3"/>
        </linearGradient>
      </defs>
      <path d="M0,0 H285 C330,200 520,420 1000,455 V550 H0 Z" fill="url(#darkPanel)"/>
      <path d="M298,0 C352,205 550,405 960,448" fill="none" stroke="url(#swooshGlow)" stroke-width="7" stroke-linecap="round"/>
    </svg>

    <div class="brand-mark">
      <span class="brand-square"></span>
      <span class="brand-name">Cedar Ridge Mechanical</span>
    </div>

    <div class="contact-block">
      <h1 class="person-name">DANIEL HAYES</h1>
      <p class="person-title">Managing Director</p>
      <p class="address">Your address, City<br>State, Zip 1234</p>
      <ul class="contact-list">
        <li>
          <svg class="contact-icon" viewBox="0 0 24 24"><path d="M6.6 10.8a15.1 15.1 0 0 0 6.6 6.6l2.2-2.2a1 1 0 0 1 1-.25 11.4 11.4 0 0 0 3.6.6 1 1 0 0 1 1 1V20a1 1 0 0 1-1 1A17 17 0 0 1 3 4a1 1 0 0 1 1-1h3.5a1 1 0 0 1 1 1c0 1.25.2 2.45.6 3.6a1 1 0 0 1-.25 1z"/></svg>
          <span>123 456 789</span>
        </li>
        <li>
          <svg class="contact-icon" viewBox="0 0 24 24"><path d="M2 5h20v14H2z M4 7v.4l8 5 8-5V7z" fill-rule="evenodd"/></svg>
          <span>info@yourgmail.com</span>
        </li>
        <li>
          <svg class="contact-icon" viewBox="0 0 24 24"><circle cx="12" cy="12" r="10"/></svg>
          <span>www.yourwebsite.com</span>
        </li>
      </ul>
    </div>
  </div>
</body>
</html>
```